design a construction company business card

Design business card around our logo. Card must have all the typical info: name, title, address, phone, email, business name, etc. Somewhere on the card I would like to see our motto "Built on integrity... Inspired by commitment." Consider adding a splash of bright orange to the card to complement the blues and silvers/grays in the logo. We are open to metallic inks, textures, etc. We would like to see options on both light and dark backgrounds. The font in the logo is Euro Technic Extended Regular.

```html
<!DOCTYPE html>
<html lang="en">
<head>
<meta charset="utf-8">
<title>Halden Contracting – Business Card</title>
<link href="https://fonts.googleapis.com/css2?family=Roboto:wght@400;500;700&display=swap" rel="stylesheet">
<style>
  :root {
    --page-bg: #f7f7f7;
    --card-navy: #0e1731;
    --brand-blue: #2a6cc4;
    --accent-orange: #f26a2e;
    --text-white: #ffffff;
    --card-shadow: 0 14px 22px rgba(0, 0, 0, 0.35);
  }
  * { margin: 0; padding: 0; box-sizing: border-box; }
  html, body {
    width: 1200px; height: 1000px; overflow: hidden;
    background: var(--page-bg);
    font-family: "Roboto", Arial, sans-serif;
  }
  .canvas { position: relative; width: 1200px; height: 1000px; }
  .card {
    position: absolute;
    background: var(--card-navy);
    box-shadow: var(--card-shadow);
    overflow: hidden;
  }
  .card--front { left: 258px; top: 89px; width: 684px; height: 390px; }
  .card--back { left: 255px; top: 527px; width: 690px; height: 393px; }

  .wordmark {
    position: absolute;
    text-align: center;
    color: var(--brand-blue);
    font-weight: 500;
    line-height: 1;
  }
  .wordmark__name { display: block; letter-spacing: 4px; }
  .wordmark__sub { display: block; letter-spacing: 2px; }
  .card--front .wordmark { left: 0; width: 684px; top: 232px; }
  .card--front .wordmark__name { font-size: 62px; }
  .card--front .wordmark__sub { font-size: 19px; margin-top: 10px; }
  .card--back .wordmark { left: 56px; width: 220px; top: 190px; }
  .card--back .wordmark__name { font-size: 44px; letter-spacing: 3px; }
  .card--back .wordmark__sub { font-size: 14px; margin-top: 8px; letter-spacing: 1px; }

  .motto {
    position: absolute; left: 24px; right: 26px; top: 349px;
    display: flex; align-items: center; gap: 14px;
    color: var(--accent-orange); font-size: 16px; white-space: nowrap;
  }
  .motto__rule { flex: 1; height: 1px; background: var(--accent-orange); }

  .contact { position: absolute; left: 388px; top: 84px; color: var(--text-white); }
  .contact__name { color: var(--brand-blue); font-size: 27px; font-weight: 500; line-height: 1.1; }
  .contact__title { font-size: 17px; margin-top: 4px; }
  .contact__title em { font-style: normal; color: var(--brand-blue); font-weight: 500; }
  .contact__list { list-style: none; margin-top: 20px; }
  .contact__item { display: flex; align-items: center; gap: 8px; font-size: 17px; height: 28px; letter-spacing: 0.2px; }
  .contact__item svg { width: 20px; height: 20px; fill: var(--brand-blue); flex: none; }
  .contact__domain { color: var(--accent-orange); }

  .wave { position: absolute; left: 0; top: 0; }
  .address {
    position: absolute; left: 388px; top: 326px;
    color: var(--text-white); font-size: 17px; line-height: 24px; letter-spacing: 0.2px;
  }
</style>
</head>
<body>
<main class="canvas">

  <section class="card card--front">
    <div class="wordmark">
      <span class="wordmark__name">HALDEN</span>
      <span class="wordmark__sub">CONTRACTING, INC.</span>
    </div>
    <p class="motto"><span class="motto__rule"></span>Built on Integrity. Inspired by Commitment<span class="motto__rule"></span></p>
  </section>

  <section class="card card--back">
    <svg class="wave" width="690" height="393" viewBox="0 0 690 393" aria-hidden="true">
      <path d="M0,350 C110,352 210,346 282,334 C215,356 115,364 0,370 Z" fill="var(--accent-orange)"/>
      <path d="M0,382 C150,380 262,368 340,345 C452,306 560,290 690,300 L690,393 L0,393 Z" fill="var(--brand-blue)"/>
    </svg>

    <div class="wordmark">
      <span class="wordmark__name">HALDEN</span>
      <span class="wordmark__sub">CONTRACTING, INC.</span>
    </div>

    <div class="contact">
      <h1 class="contact__name">Marcus Reyel</h1>
      <p class="contact__title">CEO of <em>Halden Contracting, INC</em></p>
      <ul class="contact__list">
        <li class="contact__item">
          <svg viewBox="0 0 24 24"><path d="M6.6 10.8a15.1 15.1 0 0 0 6.6 6.6l2.2-2.2c.3-.3.7-.4 1-.2 1.1.4 2.3.6 3.6.6.6 0 1 .4 1 1V20c0 .6-.4 1-1 1A17 17 0 0 1 3 4c0-.6.4-1 1-1h3.5c.6 0 1 .4 1 1 0 1.3.2 2.5.6 3.6.1.3 0 .7-.2 1z"/></svg>
          (02) 5550 1482
        </li>
        <li class="contact__item">
          <svg viewBox="0 0 24 24"><path d="M7 1h10a2 2 0 0 1 2 2v18a2 2 0 0 1-2 2H7a2 2 0 0 1-2-2V3a2 2 0 0 1 2-2zm0 3v14h10V4zm5 15.2a1.2 1.2 0 1 0 0 2.4 1.2 1.2 0 0 0 0-2.4z"/></svg>
          0400 555 217
        </li>
        <li class="contact__item">
          <svg viewBox="0 0 24 24"><path d="M2 5h20v2l-10 6L2 7zm0 4.3 10 6 10-6V19H2z"/></svg>
          info@haldencontracting.com
        </li>
        <li class="contact__item">
          <svg viewBox="0 0 24 24"><path d="M12 2a10 10 0 1 0 0 20 10 10 0 0 0 0-20zm-1 17.9A8 8 0 0 1 4.2 10l4.8 4.8v1a2 2 0 0 0 2 2zm6.9-2.5A2 2 0 0 0 16 16h-1v-3a1 1 0 0 0-1-1H8v-2h2a1 1 0 0 0 1-1V7h2a2 2 0 0 0 2-2v-.4a8 8 0 0 1 2.9 12.8z"/></svg>
          <span>www.<span class="contact__domain">haldencontracting</span>.com</span>
        </li>
      </ul>
    </div>

    <address class="address" style="font-style:normal">18/4 Ferris Ln, Westbrook<br>NSW 2190, NY</address>
  </section>

</main>
</body>
</html>
```